Small Business Directory Site Requires a Professional Responsive Web Design

Small Business Directory and Coupon Site - we require a complete website design for a brand new responsive & mobile friendly website. We already have a coder who will professional code our website in Magento.

All PSD pages need to be professionally designed then uploaded into a sharedrive (i.e. like filecrate). Additionally, as I cannot pre-empt everything, please note that we may require a little more assistance once the files have been transferred (for example, in www.brightlane-listings.example if you hover your mouse on the search box you will see a pop up box. We want one of these too and I think that means there may be extra design work here)

We have some draft page sketches have been created (there are some minor changes we want to the sketches provided though); however, we require an excellent designer to add the creative touches to it to make it look professionally created. All artwork/font must be legal.

-------------------------
We like the look of the www.brightlane-listings.example and www. marlowfolio.example

For the headers, please consider a font similar to RNS camellia. We likes this style, but it is too thin for the headers...so we need a variation like this one. For the copy/general text font, something basic that marries well with the headers.

---------------------

Please be sure to also read the brief we wrote for the coder as this will help with better understanding our design requirements.

In total I believe we have about 50 pages. This includes all the little pages and most of the pop up boxes (but not the little help key boxes). For example, pages include...

1. Login (this is where customers log in and can edit, manage their profiles. This means that there are backend membership pages)
2. Mini Services (same look and feel as the business coupons)
3. Resource Centre
4. Join (this is where customers learn about the packages available to submit a directory listing, if they ‘buy’ a package (i.e. free, $25 or $150 package) then they can create their own directory listing)
5. Search the directory (customer can view all the categories and also search the directory)
6. Create a directory listing (this is where customers learn about the packages available to submit a directory listing, if they ‘buy’ a package (i.e. free, $25 or $150 package) then they can create their own directory listing)
7. Quote finder (also know as Get a Quote)
8. Coupons (customer go to the business coupon page and can view all current coupons/submit a coupon)
9. Submit a coupon (form)
10.Advertise with us (form)
11. Join the forum
12.Submit an article or video (form)
13. Affiliates (listing of affiliates we currently have)
14. Become an affiliate (form)
15. Case studies (customer can view the case studies we have in the resource centre)
16. Help Guides (customer can view the help guides we have in the resource centre)
17. About Us
18 .Contact Us (form)
19. Terms & Condition
20. Privacy Policy
21. Supporting City Councils
22. Site Map
23. Forgot password / login details
24. Homepage
25. If we hover over a few areas (i.e. search box, location field) it pops up with more information.
etc etc etc. . . there are more pages.

Please see our filecrate link for the draft mock up pages that I have created so far.

https://www.cloudtrunk.example/sh/qk72pmw4rtz8nd/KLMvbTq2fWndxPzs8Yh4ecRQu

We are in a rush! We'd like to get the majority of the artwork completed by the end of the month. Minor fixes/tweaks can occur thereafter.

Target Market(s)

Small Businesses (employees 0 - 50) located throughout Australia

Industry/Entity Type

Business

Font styles to use
Sans Serif

Requirements
Must have
• Professional. Artwork must be legal (cannot be cut and paste or taken off other websites, must be legally purchased and used).Must look contemporary, fresh, modern.

Absolutely must be a responsive site!
Nice to have
• original work, original photos, original art.

like modern, fresh photos that demonstrate innovation, growth, small business, Australian scenery, stability, goals/passion.
Should not have
• cut and paste graphics, illegal graphics, not purchased graphics.

```html
<!DOCTYPE html>
<html lang="en">
<head>
<meta charset="utf-8">
<title>Tradeway Connect – Home</title>
<link href="https://fonts.googleapis.com/css2?family=Varela+Round&family=Open+Sans:wght@400;600;700&display=swap" rel="stylesheet">
<style>
:root{
  --orange:#f7941d;
  --navy:#1d2a44;
  --blue:#2b6cb0;
  --ink:#333840;
  --muted:#777c84;
  --line:#e3e5e8;
  --badge:#d5d8dc;
  --bar:#3a3f47;
  --footer:#16181c;
  --footer-bottom:#0c0d10;
  --white:#ffffff;
}
*{box-sizing:border-box;margin:0;padding:0}
html,body{width:779px;height:1200px;overflow:hidden;background:var(--white)}
body{font-family:"Open Sans",Arial,sans-serif;color:var(--ink);font-size:9px;position:relative}
.heading{font-family:"Varela Round","Open Sans",sans-serif;font-weight:400}
.block{position:absolute;left:0;right:0}

/* header */
.site-header{top:0;height:46px;display:flex;align-items:center;justify-content:space-between;padding:0 28px 0 34px}
.brand{display:flex;align-items:center;gap:7px}
.brand-mark{width:22px;height:22px;background:var(--orange);border-radius:3px}
.brand-name{font-weight:700;font-size:15px;color:var(--navy)}
.main-nav{display:flex;font-size:9.5px;font-weight:600;color:var(--navy)}
.main-nav a{padding:0 7px;border-left:1px solid var(--line)}
.main-nav a:first-child{border-left:none}

/* hero */
.hero{top:46px;height:310px;overflow:hidden}
.hero-photo{position:absolute;inset:0;background:linear-gradient(180deg,#1b2d55 0%,#3b4f86 45%,#6b5a8a 72%,#22263a 100%)}
.hero-copy{position:absolute;left:34px;top:96px;color:var(--white)}
.hero-copy h1{font-size:31px;line-height:1}
.hero-copy p{font-size:13px;margin-top:6px;color:#f3f3f3}
.search-bar{position:absolute;left:34px;top:178px;width:340px;height:32px;background:var(--orange);border-radius:3px;display:flex;align-items:center;gap:5px;padding:0 6px}
.search-field{height:20px;background:var(--white);border-radius:2px;font-size:7.5px;color:var(--muted);display:flex;align-items:center;padding:0 6px}
.search-field.what{width:130px}
.search-field.where{width:110px}
.search-go{width:20px;height:20px;background:var(--navy);border-radius:2px;display:flex;align-items:center;justify-content:center}
.join-btn{height:20px;padding:0 10px;background:var(--navy);color:var(--white);font-size:8.5px;font-weight:700;display:flex;align-items:center;border-radius:2px}
.listing-card{position:absolute;left:525px;top:70px;width:156px;height:210px;background:rgba(20,26,40,.9);border-radius:4px;padding:12px 10px;color:var(--white)}
.listing-card h3{font-size:11.5px;text-align:center;line-height:1.3}
.listing-card .card-photo{height:70px;margin:10px 0 8px;background:linear-gradient(135deg,#c9ccd2,#8b93a3)}
.listing-card .small{font-size:6.5px;color:#cfd3da;line-height:1.5}
.listing-card .price{font-size:16px;color:var(--orange);font-weight:700;margin-top:6px}
.listing-card .price span{font-size:8px;color:#cfd3da;font-weight:400}

/* categories */
.category-bar{top:356px;height:18px;background:var(--bar);display:flex;align-items:center;font-size:7px;color:#e9eaec;padding-left:34px}
.category-bar span{padding:0 7px;border-left:1px solid #5a6069;line-height:18px}
.category-bar span:first-child{border-left:none;padding-left:0}
.category-bar .active{background:var(--orange);color:var(--white);margin-left:auto;border-left:none;padding:0 12px}

/* community */
.section-title{text-align:center;font-size:17px;color:var(--navy)}
.community-title{top:424px}
.columns{top:474px;display:flex;gap:28px;padding:0 34px}
.col{flex:1;text-align:center}
.col h4{font-size:11.5px;color:var(--blue);line-height:1.25;height:30px}
.col-photo{height:130px;margin-bottom:10px}
.photo-desk{background:linear-gradient(135deg,#e9eef3,#aab8c6)}
.photo-handshake{background:linear-gradient(135deg,#d8dde4,#6c7a8c)}
.partner-badge{height:130px;margin-bottom:10px;display:flex;align-items:center;justify-content:center}
.partner-badge i{width:120px;height:44px;border-radius:4px;background:var(--badge);display:block}
.col p{font-size:7.5px;line-height:1.6;color:var(--muted);text-align:left;height:54px}
.btn{display:inline-block;background:var(--orange);color:var(--white);font-size:7.5px;font-weight:700;padding:6px 14px;border-radius:2px;text-transform:uppercase}

/* coupons */
.coupons-title{top:758px}
.coupon-row{top:796px;display:flex;gap:18px;padding:0 34px}
.coupon{flex:1;border:1px solid var(--line);padding:7px;text-align:center;height:102px}
.coupon-photo{height:50px}
.c1{background:linear-gradient(135deg,#f2e6c9,#c9a86a)}
.c2{background:linear-gradient(135deg,#dfe9f2,#7f9cb8)}
.c3{background:linear-gradient(135deg,#e9f0de,#9cb478)}
.c4{background:linear-gradient(135deg,#efe0e3,#b9868f)}
.coupon h5{font-size:9.5px;color:var(--navy);margin-top:5px}
.coupon p{font-size:6.5px;color:var(--muted);margin-top:2px}
.coupon .value{font-size:11px;font-weight:700;color:var(--ink);margin-top:3px}

/* sponsors */
.sponsors{top:922px;height:56px;border-top:1px solid var(--line);display:flex;justify-content:center;align-items:center;gap:100px}
.sponsors i{width:84px;height:22px;border-radius:3px;background:var(--badge);display:block}

/* footer */
.site-footer{top:988px;height:212px;background:var(--footer);color:#b9bcc2}
.footer-cols{display:flex;padding:22px 34px 0;gap:20px}
.footer-col{flex:1}
.footer-col h6{font-size:8.5px;color:var(--orange);font-weight:700;margin-bottom:8px;text-transform:uppercase}
.footer-col li{list-style:none;font-size:7.5px;line-height:1.95}
.social{display:flex;gap:5px}
.social i{width:17px;height:17px;border-radius:2px;display:block}
.s1{background:#3b5998}.s2{background:#1da1f2}.s3{background:#c4302b}.s4{background:#0077b5}
.subscribe{display:inline-block;margin-top:12px;background:var(--orange);color:var(--white);font-size:7.5px;font-weight:700;padding:6px 10px;border-radius:2px}
.footer-bottom{position:absolute;bottom:0;left:0;right:0;height:24px;background:var(--footer-bottom);font-size:7px;color:#80848b;display:flex;align-items:center;padding-left:34px}
</style>
</head>
<body>

<header class="block site-header">
  <div class="brand"><span class="brand-mark"></span><span class="brand-name">Tradeway Connect</span></div>
  <nav class="main-nav">
    <a>Login</a><a>Join</a><a>Coupons</a><a>Mini Service</a><a>Get a Quote</a><a>Advertise</a><a>Resource Centre</a>
  </nav>
</header>

<section class="block hero">
  <div class="hero-photo" role="img" aria-label="City skyline at night with a lit bridge over the harbour"></div>
  <div class="hero-copy">
    <h1 class="heading">It's a Brand New Day</h1>
    <p>Do More of What Your Love</p>
  </div>
  <div class="search-bar">
    <div class="search-field what">What are you looking for?</div>
    <div class="search-field where">Where?</div>
    <div class="search-go">
      <svg width="10" height="10" viewBox="0 0 10 10"><circle cx="4" cy="4" r="3" fill="none" stroke="#fff" stroke-width="1.4"/><line x1="6.2" y1="6.2" x2="9.2" y2="9.2" stroke="#fff" stroke-width="1.4"/></svg>
    </div>
    <div class="join-btn">Join Us</div>
  </div>
  <aside class="listing-card">
    <h3 class="heading">Create a Directory Listing today</h3>
    <div class="card-photo" role="img" aria-label="Small business owner working at a laptop"></div>
    <div class="small">LISTINGS FROM ONLY<br>Reach local customers across Australia</div>
    <div class="price">$25<span>/Year</span></div>
  </aside>
</section>

<nav class="block category-bar">
  <span>Banking, Finance &amp; Insurance</span>
  <span>Marketing, Design, Photography, Video &amp; Print</span>
  <span>Coaching &amp; Training</span>
  <span>Technology</span>
  <span>Legal</span>
  <span>Administration</span>
  <span class="active">View All Categories</span>
</nav>

<h2 class="block heading section-title community-title">Get Real Support from Our Community</h2>
<section class="block columns">
  <div class="col">
    <h4 class="heading">How Do You Sort Your Business?</h4>
    <div class="col-photo photo-desk" role="img" aria-label="Tidy office desk with notebook and coffee"></div>
    <p>Start your search with our directory of local small business experts. Compare services, read reviews from other owners and find the right help for your business, all in one easy place.</p>
    <span class="btn">Look First</span>
  </div>
  <div class="col">
    <h4 class="heading">Why Go with Tradeway Connect?</h4>
    <div class="col-photo photo-handshake" role="img" aria-label="Business people shaking hands in a bright office"></div>
    <p>We connect owners with trusted service providers, practical guides and exclusive coupon deals. Join a growing community that shares ideas and helps every small business grow.</p>
    <span class="btn">Find Out More Today</span>
  </div>
  <div class="col">
    <h4 class="heading">Become an Affiliate</h4>
    <div class="partner-badge" role="img" aria-label="Affiliate partner badge"><i></i></div>
    <p>If you have a network of small businesses, let us help you make a real difference to your members and earn rewards for every referral. Talk to us today about working together.</p>
    <span class="btn">Learn More</span>
  </div>
</section>

<h2 class="block heading section-title coupons-title">Featured Business Coupons</h2>
<section class="block coupon-row">
  <div class="coupon"><div class="coupon-photo c1" role="img" aria-label="Coupon offer photo"></div><h5 class="heading">Coupon Title</h5><p>Lorem ipsum dolor sit amet</p><div class="value">$3,000</div></div>
  <div class="coupon"><div class="coupon-photo c2" role="img" aria-label="Coupon offer photo"></div><h5 class="heading">Coupon Title</h5><p>Lorem ipsum dolor sit amet</p><div class="value">$3,000</div></div>
  <div class="coupon"><div class="coupon-photo c3" role="img" aria-label="Coupon offer photo"></div><h5 class="heading">Coupon Title</h5><p>Lorem ipsum dolor sit amet</p><div class="value">$3,000</div></div>
  <div class="coupon"><div class="coupon-photo c4" role="img" aria-label="Coupon offer photo"></div><h5 class="heading">Coupon Title</h5><p>Lorem ipsum dolor sit amet</p><div class="value">$3,000</div></div>
</section>

<div class="block sponsors" role="img" aria-label="Partner badges"><i></i><i></i><i></i></div>

<footer class="block site-footer">
  <div class="footer-cols">
    <div class="footer-col"><h6>Site Directory</h6><ul><li>Search the Directory</li><li>Create a Directory Listing</li><li>Quote Finder</li><li>Coupons</li><li>Submit A Coupon</li><li>Advertise with us</li></ul></div>
    <div class="footer-col"><h6>Site Directory</h6><ul><li>Join the Forum</li><li>Submit an Article or Video</li><li>Affiliates</li><li>Become an Affiliate</li><li>Case Studies</li><li>Help Guides</li></ul></div>
    <div class="footer-col"><h6>Popular Categories</h6><ul><li>Share an Item</li><li>Bookkeeping Services</li><li>Graphic Design</li><li>Legal Advice</li><li>Web Hosting</li><li>Printing Services</li></ul></div>
    <div class="footer-col"><h6>About Us</h6><ul><li>About Us</li><li>Contact Us</li><li>Terms &amp; Condition</li><li>Privacy Policy</li><li>Supporting City Councils</li><li>Site Map</li></ul></div>
    <div class="footer-col"><h6>Follow Us</h6><div class="social"><i class="s1"></i><i class="s2"></i><i class="s3"></i><i class="s4"></i></div><span class="subscribe">Subscribe to our Coupon Deals</span></div>
  </div>
  <div class="footer-bottom">© Tradeway Connect. All rights reserved. Terms of Use</div>
</footer>

</body>
</html>
```